Young, modern, highly skilled carpenter needs business card design

I need a business card design for my construction business. Its called 'Barlow Construction Services'. Im looking for a ultra modern design that incorporates B C S, the first letters of the name with only a subtle reference to carpentry. The design should reflect my high quality work and eye for detail. i have also uploaded some exmaple designs i like.

Industry/Entity Type

Construction

Requirements
Must have
• Name of business, my name, mobile number, ABN number, email address
Nice to have
• A logo incorporating the name of the business

```html
<!DOCTYPE html>
<html lang="en">
<head>
<meta charset="utf-8">
<title>Barlow Construction Services – Business Card</title>
<link rel="stylesheet" href="https://fonts.googleapis.com/css2?family=Cabin:wght@400;600&display=swap">
<style>
  :root {
    --backdrop: #7e8c8b;
    --card: #ffffff;
    --ink: #3a3f3a;
    --accent: #f5d000;
  }
  * { margin: 0; padding: 0; box-sizing: border-box; }
  html, body {
    width: 1200px;
    height: 900px;
    overflow: hidden;
  }
  body {
    position: relative;
    background: var(--backdrop);
    font-family: "Cabin", sans-serif;
    color: var(--ink);
  }
  .card {
    position: absolute;
    background: var(--card);
  }
  .card--front {
    left: 334px; top: 60px;
    width: 562px; height: 368px;
    display: flex;
    align-items: center;
    justify-content: center;
  }
  .card--back {
    left: 334px; top: 460px;
    width: 560px; height: 370px;
  }
  .brand {
    display: flex;
    align-items: center;
    gap: 12px;
    font-weight: 600;
    color: var(--ink);
    white-space: nowrap;
  }
  .brand__square {
    display: block;
    background: var(--accent);
  }
  .brand--front { font-size: 25px; }
  .brand--front .brand__square { width: 24px; height: 24px; }
  .contact {
    position: absolute;
    left: 70px; top: 53px;
    font-size: 20px;
    line-height: 27px;
  }
  .contact__name {
    color: var(--accent);
    font-weight: 600;
    font-size: 19px;
  }
  .contact__divider { color: var(--accent); }
  .brand--back {
    position: absolute;
    left: 70px; bottom: 40px;
    font-size: 19px;
    gap: 10px;
  }
  .brand--back .brand__square { width: 18px; height: 18px; }
</style>
</head>
<body>
  <section class="card card--front" aria-label="Card front">
    <div class="brand brand--front">
      <span class="brand__square" aria-hidden="true"></span>
      <span class="brand__name">Barlow Construction Services</span>
    </div>
  </section>

  <section class="card card--back" aria-label="Card back">
    <div class="contact">
      <p class="contact__name">Liam Barlow</p>
      <p class="contact__email">liam_barlow@mailhub.com</p>
      <p class="contact__numbers">0418 526307 <span class="contact__divider">//</span> ABN 51 824 630 172</p>
    </div>
    <div class="brand brand--back">
      <span class="brand__square" aria-hidden="true"></span>
      <span class="brand__name">Barlow Construction Services</span>
    </div>
  </section>
</body>
</html>
```